Velvet Riot Rising Line of Sparkling Wine & Spirits

Back info: Nora Beth Quill Owner 555-318-4402 1480 E. Harlow Ave, Bldg. 2, & 3, Lodi Ca. 95871
Sparkling Wines & Memorabilia www.velvetriotrising.com
Ok I have uploaded the winning design. The color that I am after is the Fushia, Raspberry, Red, Matte Satin Matalic Finish. With a 24 Karet Gold color Foil. The Bottle is on the top row and it's the 2nd Bottle in. That is the Color that I want. This is the style of font. Make sure that you put what we're advertising. Good Luck to you all. Warmest regards, Nora
21 & up UniSex
Sparkling Wine and Memorabilia
there listed up above.....

```html
<!DOCTYPE html>
<html lang="en">
<head>
<meta charset="utf-8">
<title>Velvet Riot Rising — Business Card</title>
<link href="https://fonts.googleapis.com/css2?family=Arimo:wght@400;700&display=swap" rel="stylesheet">
<style>
  :root {
    --backdrop: #e6e6e6;
    --fuchsia-core: #e21c92;
    --fuchsia-edge: #961049;
    --gold: #f2d465;
    --white: #ffffff;
    --ink: #3a3a3a;
    --ink-soft: #2b2b2b;
    --rule: #b9b9b9;
    --raspberry: #d8157f;
  }
  * { box-sizing: border-box; margin: 0; padding: 0; }
  html, body { width: 1200px; height: 1200px; overflow: hidden; }
  body {
    background: var(--backdrop);
    font-family: "Arimo", Arial, sans-serif;
    position: relative;
  }
  .card {
    position: absolute;
    left: 256px;
    width: 688px;
    height: 393px;
    overflow: hidden;
  }
  .card--front {
    top: 159px;
    background: radial-gradient(ellipse 60% 70% at 50% 45%, var(--fuchsia-core) 0%, #c71681 55%, var(--fuchsia-edge) 100%);
  }
  .card--back {
    top: 653px;
    background: var(--white);
    border-right: 2px solid var(--fuchsia-edge);
    border-bottom: 2px solid var(--fuchsia-edge);
  }
  .identity {
    position: absolute;
    top: 148px;
    left: 0; right: 0;
    text-align: center;
    white-space: nowrap;
  }
  .identity__name {
    color: var(--gold);
    font-weight: 700;
    font-size: 28px;
    letter-spacing: 0.3px;
  }
  .identity__slash {
    color: var(--gold);
    font-size: 28px;
    margin: 0 6px;
  }
  .identity__role {
    color: var(--white);
    font-size: 18px;
  }
  .contact {
    position: absolute;
    top: 200px;
    left: 0; right: 0;
    color: var(--white);
    font-size: 16.5px;
    line-height: 21px;
  }
  .contact__address {
    position: absolute;
    right: 360px;
    text-align: right;
    white-space: nowrap;
  }
  .contact__divider {
    position: absolute;
    left: 345px;
    top: 0;
    width: 1px;
    height: 47px;
    background: var(--white);
    opacity: 0.85;
  }
  .contact__lines {
    position: absolute;
    left: 362px;
    white-space: nowrap;
  }
  .contact__line { display: flex; align-items: center; gap: 9px; }
  .contact__icon { width: 15px; height: 15px; flex: none; }
  .bottle-art {
    position: absolute;
    left: 91px;
    top: 69px;
    width: 82px;
    height: 260px;
    border-radius: 14px 14px 10px 10px;
    background: linear-gradient(90deg, #b0105f 0%, #e5259a 45%, #c01370 100%);
  }
  .brand {
    position: absolute;
    left: 192px;
    top: 170px;
    color: var(--ink-soft);
    font-weight: 700;
    font-size: 40px;
    white-space: nowrap;
  }
  .brand__rule {
    position: absolute;
    left: 178px;
    top: 226px;
    width: 440px;
    height: 1px;
    background: linear-gradient(90deg, var(--rule) 0%, var(--rule) 70%, rgba(185,185,185,0) 100%);
  }
  .tagline {
    position: absolute;
    left: 192px;
    top: 238px;
    font-size: 17px;
    letter-spacing: 2.2px;
    white-space: nowrap;
    color: var(--ink);
  }
  .tagline__accent { color: var(--raspberry); font-weight: 700; }
</style>
</head>
<body>
  <section class="card card--front" aria-label="Card front">
    <div class="identity">
      <span class="identity__name">NORA BETH QUILL</span><span class="identity__slash">/</span><span class="identity__role">Owner</span>
    </div>
    <div class="contact">
      <div class="contact__address">1480 E. Harlow Ave<br>Bldg. 2, &amp; 3, Lodi Ca. 95871</div>
      <div class="contact__divider"></div>
      <div class="contact__lines">
        <div class="contact__line">
          <svg class="contact__icon" viewBox="0 0 16 16" aria-hidden="true"><path fill="#f2d465" d="M3.2 1.2l2.4-.4 1.3 3.3-1.6 1.2c.8 1.8 2.2 3.2 4 4l1.2-1.6 3.3 1.3-.4 2.4c-.2.9-1 1.4-1.9 1.4C6 12.6 3.4 10 3.2 4.5c0-.9.1-2.9 0-3.3z"/></svg>
          <span>555-318-4402</span>
        </div>
        <div class="contact__line">
          <svg class="contact__icon" viewBox="0 0 16 16" aria-hidden="true"><circle cx="8" cy="8" r="7" fill="#f2d465"/><path fill="#c71681" d="M5 4c1.5 0 2 1 1.6 2S4.5 7 4.6 8.4 6.4 10 6 12c-1.8-.6-3-2.2-3-4.2C3 6 3.8 4.6 5 4zm5 4c1 .2 1.8 1 1.4 2.3-.3.8-1.2 1-1.6.3C9.5 10 9 8.8 10 8z"/></svg>
          <span>www.velvetriotrising.com</span>
        </div>
      </div>
    </div>
  </section>

  <section class="card card--back" aria-label="Card back">
    <div class="bottle-art" role="img" aria-label="Illustration of a fuchsia sparkling wine bottle with gold foil neck"></div>
    <div class="brand">Velvet Riot Rising</div>
    <div class="brand__rule"></div>
    <div class="tagline">SPARKLING <span class="tagline__accent">WINES &amp; MEMORABILIA</span></div>
  </section>
</body>
</html>
```